Clean Vexlo Ads Banner Design For A Finance Company

Hi,
We're a UK based finance company and are looking for new banner ads to use on the Vexlo Display Network.
We want the end product to stand out by using strong, minimal design - ideally starting from a dark theme, although I'm open to ideas.
The copy should read:
'Fast Bridging Loans From 0.39% PM'
Once we have these designs agreed, we are looking to replicate them for other products, changing only the text on each ad - for example, 'commercial mortgage service you can rely on' or 'development finance service you can rely on'.
The colours used on our website are the following:
Black - #040303
Orange - #f79124
White - #ffffff
Grey - #ffffff
Example ads that I like - https://www.plimrake.com/wp-content/uploads/2021/07/vexlo-display-ads-example-2-final.png.webp
2 - https://qarnelvistahub.com/wp-content/uploads/2020/03/fbdd56ba3bd16c7a8debb13a411de786.jpg

```html
<!DOCTYPE html>
<html lang="en">
<head>
<meta charset="utf-8">
<title>Norvale Finance – Fast Bridging Loans</title>
<link rel="stylesheet" href="https://fonts.googleapis.com/css2?family=Libre+Bodoni:wght@700&display=swap">
<style>
  :root {
    --black: #040303;
    --orange: #f79124;
    --white: #ffffff;
    --photo-light: #3a3430;
    --photo-mid: #1c1a19;
  }
  * { margin: 0; padding: 0; box-sizing: border-box; }
  html, body {
    width: 1199px;
    height: 1200px;
    overflow: hidden;
    background: var(--black);
  }
  .banner {
    position: relative;
    width: 1199px;
    height: 1200px;
    overflow: hidden;
    background: var(--black);
    font-family: "Libre Bodoni", "Bodoni Moda", Georgia, serif;
    font-weight: 700;
    color: var(--white);
  }
  .banner__photo {
    position: absolute;
    inset: 0;
    background:
      radial-gradient(ellipse 420px 700px at 260px 640px, rgba(70,62,56,0.55), rgba(4,3,3,0) 70%),
      linear-gradient(90deg, var(--photo-light) 0%, var(--photo-mid) 30%, var(--black) 55%, var(--black) 100%);
  }
  .brand {
    position: absolute;
    left: 506px;
    top: 58px;
    width: 558px;
    height: 264px;
    background: var(--black);
    display: flex;
    align-items: center;
    justify-content: center;
  }
  .brand__name {
    color: var(--orange);
    font-size: 52px;
    letter-spacing: 1px;
    text-align: center;
    line-height: 1.15;
  }
  .headline {
    position: absolute;
    left: 541px;
    line-height: 1;
    white-space: nowrap;
  }
  .headline--fast     { top: 443px; font-size: 108px; }
  .headline--bridging { top: 541px; font-size: 108px; }
  .headline--loans    { top: 644px; font-size: 104px; color: var(--orange); }
  .rate__from { position: absolute; left: 543px; top: 775px; font-size: 41px; line-height: 1; }
  .rate__value {
    position: absolute;
    left: 538px;
    top: 812px;
    font-size: 188px;
    line-height: 1;
    color: var(--orange);
    letter-spacing: -2px;
  }
  .rate__unit { position: absolute; left: 548px; top: 985px; font-size: 41px; line-height: 1; }
</style>
</head>
<body>
  <main class="banner">
    <div class="banner__photo" role="img" aria-label="Photograph of a confident businessman in a dark suit and red tie, arms folded, against a dark backdrop"></div>

    <div class="brand">
      <span class="brand__name">Norvale Finance<br>Limited</span>
    </div>

    <h1>
      <span class="headline headline--fast">FAST</span>
      <span class="headline headline--bridging">BRIDGING</span>
      <span class="headline headline--loans">LOANS</span>
    </h1>

    <p class="rate">
      <span class="rate__from">FROM</span>
      <span class="rate__value">0.39%</span>
      <span class="rate__unit">PM</span>
    </p>
  </main>
</body>
</html>
```